Real Estate Company Looking for Business Card Designs for 3 Executives

Hello!
Thanks so much for considering our project! We are a real estate investment company located in Edmonton, Alberta called Bellhaven Group of Companies. We invest/develop both commercial and residential real estate and are looking to create 3 DOUBLE-SIDED business cards for 3 top executives in the company! (for some reason it won't let us select the double-sided option, but yes, the cards are double sided and would be happy to tip extra)

We have certain guidelines that we want our business cards to for sure follow - the back of the Business card has to be the Black Background Version of the Logo which has already been designed and linked as a file (first file). We want the entire back of the card to simply just be the black background logo. In terms of the front of the card, would like to see a smaller version of the white background logo (linked as the second file) in the top left hand corner - of course, feel free to get creative and we can make revisions together along the way! and Then after that, just text. We want the card to be sharp, clean, easy on the eyes and highly professional looking. We would like the card to include the Full name of the Company (Bellhaven Group of Companies), Name of the Person, Title, Phone, Email. If possible please provide the front part of the card for 3 people:

1) Bellhaven Group of Companies, Liora Quenby, Chief Financial Officer, 780-555-0142, lioraquenby@bellhavengroup.example

2) Bellhaven Group of Companies, Tobias Quenby, Chief Executive Officer, 780-555-0187, tobiasquenby@bellhavengroup.example

3) Bellhaven Group of Companies, Rui Delcourt, Chief Operations Officer, 587-555-0163, ruidelcourt@bellhavengroup.example

Thank you so much for considering our project & we look forward to seeing your designs!

```html
<!DOCTYPE html>
<html lang="en">
<head>
<meta charset="utf-8">
<title>Bellhaven Business Card</title>
<link href="https://fonts.googleapis.com/css2?family=Karla:ital,wght@0,400;0,500;1,400;1,500&display=swap" rel="stylesheet">
<style>
  :root {
    --stage: #8e8e8e;
    --card-front: #ffffff;
    --card-back: #333333;
    --ink: #111111;
    --ink-soft: #222222;
    --tree-tone: #e6e6e6;
    --mark-back: #8a8a8a;
  }
  * { box-sizing: border-box; margin: 0; padding: 0; }
  html, body {
    width: 1200px; height: 1200px; overflow: hidden;
    background: var(--stage);
    font-family: "Karla", Arial, sans-serif;
  }
  .card {
    position: absolute; left: 262px; width: 686px; height: 392px;
    overflow: hidden;
  }
  .card--front { top: 165px; background: var(--card-front); color: var(--ink); }
  .card--back { top: 653px; background: var(--card-back); }

  .forest-art {
    position: absolute; left: 308px; top: 0; width: 378px; height: 100%;
    background: linear-gradient(90deg, #ffffff 0%, var(--tree-tone) 18%, var(--tree-tone) 82%, #f2f2f2 100%);
    opacity: .7;
  }

  .brand { position: absolute; left: 50px; top: 52px; }
  .brand__square { width: 58px; height: 58px; background: var(--ink); margin-bottom: 40px; }
  .brand__name { font-size: 16px; font-weight: 400; letter-spacing: .32em; color: var(--ink); }

  .company { position: absolute; left: 50px; top: 222px; }
  .company__name { font-size: 26px; font-weight: 500; letter-spacing: .02em; line-height: 1; }
  .company__tag { font-size: 14px; font-style: italic; font-weight: 500; letter-spacing: .04em; margin-top: 6px; }

  .contact { position: absolute; left: 50px; top: 290px; list-style: none; font-size: 14.5px; color: var(--ink-soft); }
  .contact li { display: flex; align-items: center; height: 19.5px; }
  .contact svg { width: 10px; height: 10px; margin-right: 10px; fill: var(--ink); }

  .person { position: absolute; right: 43px; top: 262px; text-align: right; }
  .person__name { font-size: 24px; font-weight: 500; letter-spacing: .04em; line-height: 1; }
  .person__title { font-size: 14px; letter-spacing: .03em; margin-top: 6px; color: var(--ink-soft); }

  .back-brand {
    position: absolute; left: 0; right: 0; top: 108px;
    display: flex; flex-direction: column; align-items: center;
  }
  .back-brand__square { width: 110px; height: 110px; background: var(--mark-back); margin-bottom: 40px; }
  .back-brand__name { font-size: 21px; letter-spacing: .6em; margin-right: -.6em; color: var(--mark-back); }
</style>
</head>
<body>
  <section class="card card--front">
    <div class="forest-art" role="img" aria-label="Faint illustration of tall pine tree trunks"></div>

    <div class="brand">
      <div class="brand__square"></div>
      <div class="brand__name">BELLHAVEN</div>
    </div>

    <div class="company">
      <div class="company__name">BELLHAVEN</div>
      <div class="company__tag">GROUP OF COMPANIES</div>
    </div>

    <ul class="contact">
      <li><svg viewBox="0 0 10 10"><path d="M2 0.5 L3.6 2.8 L2.7 3.9 C3.3 5.3 4.7 6.7 6.1 7.3 L7.2 6.4 L9.5 8 L8.4 9.5 C4.5 9.5 0.5 5.5 0.5 1.6 Z"/></svg>780-555-0142</li>
      <li><svg viewBox="0 0 10 10"><path d="M0.5 2 H9.5 V8.5 H0.5 Z M0.9 2.4 L5 5.6 L9.1 2.4" stroke="#fff" stroke-width=".9"/></svg>lioraquenby@bellhavengroup.example</li>
      <li><svg viewBox="0 0 10 10"><circle cx="5" cy="5" r="4.5"/><path d="M0.5 5 H9.5 M5 0.5 C3 3 3 7 5 9.5 M5 0.5 C7 3 7 7 5 9.5" stroke="#fff" stroke-width=".7" fill="none"/></svg>www.bellhavengroup.example</li>
    </ul>

    <div class="person">
      <div class="person__name">LIORA QUENBY</div>
      <div class="person__title">Chief Financial Officer</div>
    </div>
  </section>

  <section class="card card--back">
    <div class="back-brand">
      <div class="back-brand__square"></div>
      <div class="back-brand__name">BELLHAVEN</div>
    </div>
  </section>
</body>
</html>
```